Business Card (double-sided) and Stationary Design for dental office

1) Business Card Design: We need a business card design for a dental specialty office.
Texts should contain:
The name of our office "Brindle Oaks Orthodontics"
Tagline: "Specialist in Orthodontic and Maxillofacial Orthopedics"
Tag line: "Creating "Tolvering" smiles for Children and Adults"
Doctor name: "Doctor Name"
Office Address:
"123 Street Name
City, State Zip code"
Office email address: office@brindleoaksortho.com
Website: www.brindleoaksortho.com

We will provide the full office address once the design is selected
Theme: beach, paradise, coastal, wave
We would like to have some creativity in design. Some acceptable ideas: front page: logo and office name. Back page: more detail information, and map to office in form of an island. Please see sample from our other location, but you DON'T HAVE TO USE OR COPY THE SAME CONCEPT.

IF POSSIBLE, PLEASE SUBMIT AT LEAST TWO CONCEPTS: ONE WITH THE BACK LOOKING SIMILAR TO WHAT IS IN THE SAMPLE, AND ONE DIFFERENT.

Color: designer to choose. We have different shade of blues and sand color in our office. Please see logo.

2) Please also design a matching set of stationary that compliment the business card and our logo.

Target Market(s)

Dental

Contact Information for Business Card

See descriptions

Font styles to use
Other font styles liked:
• Matching texts in logo

Colors
0054AA
0677BA
7BADD7
CADEEF
E8F1F8
0094D4
00A9DD
6FCCEA
C7EBF8
E9F6FB
00AB8E
00BBA5
67D7C9
C6EFE9
E9F9F6

Requirements
Must have
• Double-sided
Nice to have
• Beach coastal theme
Should not have
• Any shape or drawing of of tooth or teeth. We don’t need these. You don't necessarily have to just cut and paste the logo art and text as a whole, you have the liberty to rearrange the text.

```html
<!DOCTYPE html>
<html lang="en">
<head>
<meta charset="utf-8">
<title>Brindle Oaks Orthodontics – Business Card</title>
<link rel="stylesheet" href="https://fonts.googleapis.com/css2?family=Roboto:wght@400;500;700;900&display=swap">
<style>
  :root {
    --page-bg: #d9dadc;
    --card-white: #ffffff;
    --teal-deep: #2a86a3;
    --teal-mid: #2f95b0;
    --teal-light: #6fcfc0;
    --ink: #30343a;
    --ink-soft: #4a4f57;
    --brown-dark: #3b1414;
    --brown-tag: #3a1c0c;
    --sky-top: #6cc4ef;
    --sky-low: #cfeefb;
    --sea: #1b8fd2;
    --sea-light: #7dd3f3;
    --sand: #f4c25a;
    --sand-deep: #e9a63a;
    --panel: rgba(255, 255, 255, 0.86);
  }
  * { box-sizing: border-box; margin: 0; padding: 0; }
  html, body { width: 1200px; height: 800px; overflow: hidden; }
  body {
    background: var(--page-bg);
    font-family: "Roboto", Arial, sans-serif;
    display: flex;
    align-items: center;
    justify-content: center;
    gap: 24px;
  }
  .card {
    position: relative;
    width: 564px;
    height: 322px;
    border-radius: 18px;
    overflow: hidden;
    box-shadow: 0 6px 18px rgba(0,0,0,0.18);
  }

  /* Front */
  .card-front { background: var(--card-white); }
  .front-brand {
    position: absolute;
    left: 34px; top: 92px;
    display: flex; align-items: center; gap: 12px;
  }
  .brand-dot {
    width: 54px; height: 54px; border-radius: 50%;
    background: var(--teal-mid);
    flex: none;
  }
  .brand-name {
    font-weight: 700;
    font-size: 22px;
    line-height: 1.15;
    color: var(--teal-mid);
    width: 170px;
  }
  .front-divider {
    position: absolute;
    left: 262px; top: 30px;
    width: 1px; height: 190px;
    background: linear-gradient(#e2e2e2, #c8c8c8);
  }
  .contact {
    position: absolute;
    left: 288px; top: 48px;
    color: var(--ink);
  }
  .contact-name {
    font-weight: 700; font-size: 21px; letter-spacing: 0.5px;
    color: var(--teal-deep); margin-bottom: 10px;
  }
  .contact-address { font-size: 14px; line-height: 1.3; margin-bottom: 12px; }
  .contact-line {
    display: flex; align-items: center; gap: 8px;
    font-size: 14px; line-height: 1.45;
  }
  .contact-line svg { width: 12px; height: 12px; flex: none; fill: var(--teal-deep); }
  .front-band {
    position: absolute; left: 0; right: 0; bottom: 0; height: 58px;
    background: var(--teal-mid);
    border-top: 5px solid var(--teal-light);
    display: flex; align-items: center; justify-content: center;
  }
  .front-tagline {
    color: #fff; font-weight: 700; font-size: 17.5px; letter-spacing: 0.2px;
  }

  /* Back */
  .card-back { background: var(--sand); }
  .beach-scene {
    position: absolute; inset: 0;
    background: linear-gradient(180deg,
      var(--sky-top) 0%, var(--sky-low) 38%,
      var(--sea-light) 40%, var(--sea) 52%, var(--sea-light) 62%,
      var(--sand) 66%, var(--sand-deep) 100%);
  }
  .island-map {
    position: absolute; right: 18px; top: 170px;
    width: 150px; height: 86px;
    border-radius: 10px;
    background: linear-gradient(160deg, #f6cf73, #eeb14a);
  }
  .back-brand {
    position: absolute; left: 0; right: 0; top: 40px;
    display: flex; justify-content: center; align-items: center; gap: 10px;
  }
  .back-brand .brand-dot { width: 34px; height: 34px; background: var(--brown-dark); }
  .back-brand .brand-name {
    width: auto; font-size: 22px; color: var(--brown-dark);
  }
  .appointment {
    position: absolute; left: 36px; top: 112px;
    width: 350px; height: 126px;
    background: var(--panel);
    border-radius: 12px;
    padding: 16px 18px;
  }
  .appointment-title {
    font-weight: 700; font-size: 15px; color: var(--teal-deep);
    letter-spacing: 0.3px; margin-bottom: 14px;
  }
  .field {
    display: flex; align-items: flex-end; gap: 4px;
    font-size: 14px; color: var(--teal-deep); margin-bottom: 12px;
  }
  .field-rule { flex: 1; border-bottom: 1px dotted var(--teal-deep); height: 1px; margin-bottom: 4px; }
  .back-tagline {
    position: absolute; left: 0; right: 0; bottom: 26px;
    text-align: center;
    font-weight: 900; font-size: 19px; color: var(--brown-tag);
  }
</style>
</head>
<body>

  <section class="card card-front">
    <div class="front-brand">
      <span class="brand-dot"></span>
      <span class="brand-name">Brindle Oaks Orthodontics</span>
    </div>
    <div class="front-divider"></div>
    <div class="contact">
      <p class="contact-name">DANIEL REYES</p>
      <p class="contact-address">123 Street Name<br>City, State Zip code</p>
      <p class="contact-line">
        <svg viewBox="0 0 24 24"><path d="M6.6 10.8a15.1 15.1 0 0 0 6.6 6.6l2.2-2.2a1 1 0 0 1 1-.25 11.4 11.4 0 0 0 3.6.57 1 1 0 0 1 1 1V20a1 1 0 0 1-1 1A17 17 0 0 1 3 4a1 1 0 0 1 1-1h3.5a1 1 0 0 1 1 1c0 1.25.2 2.45.57 3.57a1 1 0 0 1-.25 1z"/></svg>
        555-214-7390
      </p>
      <p class="contact-line">
        <svg viewBox="0 0 24 24"><path d="M2 5h20v14H2z M2 5l10 8 10-8" /></svg>
        office@brindleoaksortho.com
      </p>
      <p class="contact-line">
        <svg viewBox="0 0 24 24"><circle cx="12" cy="12" r="10"/></svg>
        www.brindleoaksortho.com
      </p>
    </div>
    <div class="front-band">
      <p class="front-tagline">Specialist in Orthodontic &amp; Maxillofacial Orthopedics</p>
    </div>
  </section>

  <section class="card card-back">
    <div class="beach-scene" role="img" aria-label="Illustrated tropical beach with sky, clouds, sea, a sandy island with palm trees and a rock"></div>
    <div class="island-map" role="img" aria-label="Hand-drawn street map to the office"></div>
    <div class="back-brand">
      <span class="brand-dot"></span>
      <span class="brand-name">Brindle Oaks Orthodontics</span>
    </div>
    <div class="appointment">
      <p class="appointment-title">SEE YOU AT YOUR NEXT APPOINTMENT!</p>
      <p class="field">For<span class="field-rule"></span></p>
      <p class="field">Date<span class="field-rule"></span>Time<span class="field-rule"></span></p>
    </div>
    <p class="back-tagline">Creating "Tolvering" smiles for Children &amp; Adults</p>
  </section>

</body>
</html>
```